4th Generation Family Business Needs a New Card Design!

We are a family owned 4th Generation company. We are based in the Sydney, Australia area and we are desperately in need of a more modern and classy card. We are monumental masons who design, supply & erect lasting memorials throughout cemeteries in Sydney. Our customers are normally in a period of grieving. I have attached logo files that will need to be implemented on the card. Company was established 1935. Australian Owned and Operated. Card needs to be designed to PIXO.com specification.

Target Market(s)

Our target market is based upon people that a grieving for family members that have passed away. We also deal with alot of companies that own and operate cemeteries.

Industry/Entity Type

Business

Contact Information for Business Card

Simon Harcourt, Operations Manager, 0417293086, simon@harcourtmemorials.com.au
Lewis Harcourt, Director, 0491630572, lewis@harcourtmemorials.com.au
Phone # 02 9561 3048
Website: www.harcourtmemorials.com.au
Address: Suite 17, 8 Palfrey Lane, West Carlow, Sydney NSW 2156

Font styles to use
Serif
Decorative
Script

Requirements
Must have
• Would like to see the logo nicely implemented with a modern design. Embossed lettering would be a nice additive.

```html
<!DOCTYPE html>
<html lang="en">
<head>
<meta charset="utf-8">
<title>Harcourt Memorials – Business Card</title>
<link rel="stylesheet" href="https://fonts.googleapis.com/css2?family=PT+Sans:ital,wght@0,400;0,700;1,400;1,700&display=swap">
<style>
  :root {
    --backdrop: #4a4a4c;
    --stone-light: #8e8f82;
    --stone-mid: #7b7c6f;
    --stone-dark: #66675c;
    --gold: #e8b92a;
    --ink-light: #f2f2ee;
    --ink-soft: #e4e3dc;
    --shadow: rgba(0,0,0,0.55);
  }
  * { box-sizing: border-box; margin: 0; padding: 0; }
  html, body {
    width: 1200px; height: 675px; overflow: hidden;
    background: var(--backdrop);
    font-family: "PT Sans", "Helvetica Neue", Arial, sans-serif;
  }
  .canvas {
    position: relative; width: 1200px; height: 675px;
    display: flex; justify-content: center; align-items: center; gap: 40px;
  }
  .card {
    position: relative; width: 540px; height: 330px; overflow: hidden;
    box-shadow: 0 10px 24px rgba(0,0,0,0.35);
  }
  .card__stone {
    position: absolute; inset: 0;
    background:
      linear-gradient(115deg, transparent 30%, rgba(255,255,255,0.06) 45%, transparent 60%),
      linear-gradient(160deg, var(--stone-light) 0%, var(--stone-mid) 45%, var(--stone-dark) 100%);
  }
  .card__content { position: absolute; inset: 0; text-shadow: 1px 1px 1px var(--shadow); }

  /* back: contact details */
  .person { position: absolute; left: 44px; top: 146px; }
  .person__name {
    color: var(--gold); font-weight: 700; font-style: italic;
    font-size: 21px; letter-spacing: 0.3px; text-transform: uppercase; line-height: 1;
  }
  .person__role { color: var(--ink-light); font-style: italic; font-size: 14px; margin-top: 3px; }
  .rule {
    position: absolute; left: 40px; right: 36px; top: 192px;
    height: 1px; background: var(--gold);
  }
  .social { position: absolute; right: 38px; top: 172px; display: flex; gap: 5px; }
  .social__dot { width: 12px; height: 12px; border-radius: 50%; background: var(--gold); }
  .contact { position: absolute; left: 28px; top: 202px; font-size: 14.5px; line-height: 20px; }
  .contact__line { color: var(--ink-light); font-style: italic; }
  .contact__line--indent1 { padding-left: 18px; }
  .contact__line--indent2 { padding-left: 12px; }
  .contact__label { color: var(--gold); font-weight: 700; margin-right: 4px; }
  .contact__web { color: var(--gold); font-weight: 700; font-style: italic; }
  .address {
    position: absolute; right: 36px; top: 210px; text-align: right;
    color: var(--ink-soft); font-size: 15px; line-height: 19px;
  }

  /* front: brand */
  .brand {
    position: absolute; left: 0; right: 0; top: 122px;
    display: flex; flex-direction: column; align-items: center;
  }
  .brand__name {
    color: var(--ink-light); font-weight: 700; text-transform: uppercase;
    font-size: 34px; letter-spacing: 3px; line-height: 1.05; text-align: center;
  }
</style>
</head>
<body>
<main class="canvas">
  <section class="card card--back" aria-label="Card back with contact details">
    <div class="card__stone" role="img" aria-label="Grey-green natural sandstone texture"></div>
    <div class="card__content">
      <div class="person">
        <p class="person__name">Simon Harcourt</p>
        <p class="person__role">Operations Manager</p>
      </div>
      <div class="social" aria-label="Social links">
        <span class="social__dot"></span><span class="social__dot"></span><span class="social__dot"></span>
        <span class="social__dot"></span><span class="social__dot"></span><span class="social__dot"></span>
        <span class="social__dot"></span><span class="social__dot"></span>
      </div>
      <div class="rule"></div>
      <div class="contact">
        <p class="contact__line contact__line--indent1"><span class="contact__label">C :</span>0417293086</p>
        <p class="contact__line contact__line--indent2"><span class="contact__label">P :</span>02 9561 3048</p>
        <p class="contact__line">simon@harcourtmemorials.com.au</p>
        <p class="contact__web">www.harcourtmemorials.com.au</p>
      </div>
      <address class="address" style="font-style:normal">
        Suite 17, 8 Palfrey Lane<br>West Carlow<br>Sydney NSW 2156
      </address>
    </div>
  </section>

  <section class="card card--front" aria-label="Card front with company name">
    <div class="card__stone" role="img" aria-label="Grey-green natural sandstone texture"></div>
    <div class="card__content">
      <div class="brand">
        <p class="brand__name">Harcourt<br>Memorials</p>
      </div>
    </div>
  </section>
</main>
</body>
</html>
```